A private security company called "Tavron Security Services Ltd"

Hello everybody,

We need a web page for a company based in NZ. It is mainly an informative website so it would be wonderful if the designer puts their absolute best into making it a website that I would really appreciate. The website needs to show professionalism and also needs to make our web surfers find the information they need in a click. the company's colour is black and silver, and if those two colours could be integrated into the website it would be absolutely lovely. Please do contact me for any information.

Sincerely,
Dorian Vaskel

Industry/Entity Type

Security

```html
<!DOCTYPE html>
<html lang="en">
<head>
<meta charset="utf-8">
<title>Tavron Security Services Ltd</title>
<link rel="stylesheet" href="https://fonts.googleapis.com/css2?family=Arimo:wght@400;700&family=Pathway+Gothic+One&display=swap">
<style>
:root{
  --ink:#111;
  --text:#555;
  --muted:#8a8a8a;
  --silver:#e9e9e9;
  --silver-light:#f6f6f6;
  --line:#c9c9c9;
  --dark:#2b2b2b;
  --darker:#1f1f1f;
  --footer-text:#9a9a9a;
  --white:#fff;
}
*{margin:0;padding:0;box-sizing:border-box}
html,body{width:1200px;height:2266px;overflow:hidden}
body{position:relative;background:var(--white);font-family:"Arimo",Arial,sans-serif;color:var(--text)}
.display{font-family:"Pathway Gothic One","Arial Narrow",sans-serif;font-weight:400}

/* header */
.site-header{position:absolute;left:0;top:0;width:1200px;height:159px;background:linear-gradient(#fafafa,#e4e4e4);border-bottom:1px solid #d0d0d0}
.brand{position:absolute;left:157px;top:40px;display:flex;align-items:center;gap:12px}
.brand-mark{width:34px;height:34px;border-radius:50%;background:var(--ink)}
.brand-name{font-family:"Pathway Gothic One",sans-serif;color:var(--ink);font-size:30px;line-height:1;letter-spacing:3px}
.brand-name small{display:block;font-size:15px;letter-spacing:1px;margin-top:4px}
.main-nav{position:absolute;left:405px;top:100px;display:flex;font-size:12.5px;color:#333;text-transform:uppercase}
.main-nav span{margin-right:32px}
.main-nav span:last-child{margin-right:0}
.social{position:absolute;display:flex;gap:9px}
.social i{display:block;width:31px;height:31px;border-radius:50%;background:#a5a5a5}

/* hero */
.hero{position:absolute;left:0;top:159px;width:1200px;height:515px;background:radial-gradient(ellipse at 50% 35%,#5d5d5d,#3a3a3a 55%,#262626)}
.hero-photo{position:absolute;left:688px;top:60px;width:267px;height:455px;background:linear-gradient(90deg,rgba(150,150,150,.15),rgba(205,205,205,.55) 55%,rgba(150,150,150,.2));border-radius:60px 60px 0 0}
.hero-title{position:absolute;left:217px;top:225px;color:#e6e6e6;font-size:37px;line-height:47px;text-shadow:0 2px 3px rgba(0,0,0,.6)}
.hero-title b{font-weight:400;color:var(--white);font-size:42px}
.slide-arrow{position:absolute;width:50px;height:50px;border-radius:50%;background:rgba(120,120,120,.55)}
.slide-arrow svg{position:absolute;left:17px;top:14px}

/* solutions */
.solutions{position:absolute;left:0;top:674px;width:1200px;height:711px;background:linear-gradient(#f7f7f7,#dedede)}
.section-title{position:absolute;left:0;width:1200px;text-align:center;color:var(--ink);font-size:43px}
.sidebar-title{position:absolute;left:157px;top:826px;font-size:26px;color:var(--ink)}
.service-list{position:absolute;left:157px;top:885px;list-style:none;font-size:12.5px;color:#666}
.service-list li{position:absolute;left:0;width:215px;padding-left:32px;line-height:16px}
.service-list li::before{content:"";position:absolute;left:0;top:-1px;width:17px;height:17px;border-radius:50%;background:var(--white);border:1px solid #d4d4d4}
.service-list li::after{content:"";position:absolute;left:6px;top:5px;width:4px;height:4px;border-right:1.5px solid #888;border-top:1.5px solid #888;transform:rotate(45deg)}
.callout{position:absolute;left:157px;top:1096px;width:211px;height:251px;background:linear-gradient(160deg,#5b5b5b,#bdbdbd 60%,#e0e0e0);border:1px solid #999}
.callout p{position:absolute;left:17px;top:16px;font-family:"Pathway Gothic One",sans-serif;color:#e8e8e8;font-size:22px;line-height:27px;text-shadow:0 1px 2px rgba(0,0,0,.5)}
.callout p b{font-weight:400;font-size:27px}
.callout .brand{left:20px;top:176px}
.col-rule{position:absolute;width:1px;background:var(--line)}
.row-rule{position:absolute;height:1px;background:var(--line)}
.card{position:absolute;width:192px}
.card h3{font-family:"Pathway Gothic One",sans-serif;font-weight:400;font-size:23px;color:var(--ink);margin-bottom:26px}
.card p{font-size:11.3px;line-height:15.8px;color:#777;margin-bottom:15px}
.read-more{position:absolute;right:0;font-size:11px;color:#222;background:linear-gradient(#fff,#e3e3e3);border:1px solid #bbb;padding:5px 9px;border-radius:2px}

/* industries */
.industry{position:absolute;top:1530px;width:194px;height:155px;background:var(--white);border:1px solid #dcdcdc;padding:5px}
.industry div{width:100%;height:100%}
.industry-label{position:absolute;top:1691px;width:194px;text-align:center;font-size:21px;color:var(--ink)}
.carousel-btn{position:absolute;top:1590px;width:33px;height:33px;border-radius:50%;background:#b7b7b7}
.carousel-btn svg{position:absolute;left:11px;top:9px}

/* footer */
.site-footer{position:absolute;left:0;top:1788px;width:1200px;height:478px;background:radial-gradient(ellipse at 50% 0,#5a5a5a,#333 60%,#2a2a2a)}
.footer-title{position:absolute;top:1843px;font-size:31px;color:#e0e0e0}
.footer-copy{position:absolute;left:157px;top:1917px;width:306px;font-size:11.5px;line-height:15.5px;color:var(--footer-text)}
.footer-copy p{margin-bottom:15px}
.quick-links{position:absolute;left:539px;top:1910px;list-style:none;font-size:12px;color:var(--footer-text)}
.quick-links li{height:31.3px;padding-left:22px;position:relative}
.quick-links li::before{content:"";position:absolute;left:2px;top:3px;width:4px;height:4px;border-right:1.5px solid #ddd;border-top:1.5px solid #ddd;transform:rotate(45deg)}
.newsletter-note{position:absolute;left:767px;top:1914px;width:280px;font-size:11.5px;line-height:15px;color:#8c8c8c}
.field{position:absolute;left:767px;width:274px;height:34px;background:#707070;color:#e4e4e4;font-size:12px;padding:11px 19px}
.signup{position:absolute;left:767px;top:2081px;width:143px;height:34px;background:linear-gradient(#fff,#ddd);border:1px solid #999;font-size:12px;color:#222;text-align:center;line-height:32px}
.footer-bar{position:absolute;left:0;top:2175px;width:1200px;height:91px;background:var(--darker);border-top:1px solid #3d3d3d}
.copyright{position:absolute;left:157px;top:2210px;font-size:12px;color:#8f8f8f}
.social.dark i{background:#9a9a9a}
</style>
</head>
<body>

<header class="site-header">
  <div class="brand"><span class="brand-mark"></span><span class="brand-name">TAVRON<small>SECURITY SERVICES LTD.</small></span></div>
  <nav class="main-nav"><span>Home</span><span>Our Services</span><span>About</span><span>Locations</span><span>News</span><span>Careers</span><span>Contact Us</span></nav>
  <div class="social" style="left:931px;top:32px" aria-label="Social links"><i></i><i></i><i></i></div>
</header>

<section class="hero">
  <div class="hero-photo" role="img" aria-label="Security camera mounted on a steel pole"></div>
  <h1 class="hero-title display"><b>Lorem Ipsum</b> is simply dummy text of<br>the printing and typesetting industry.</h1>
  <span class="slide-arrow" style="left:105px;top:232px"><svg width="14" height="22"><path d="M12 2 3 11l9 9" fill="none" stroke="#eee" stroke-width="2"/></svg></span>
  <span class="slide-arrow" style="left:1045px;top:232px"><svg width="14" height="22"><path d="M3 2l9 9-9 9" fill="none" stroke="#eee" stroke-width="2"/></svg></span>
</section>

<section class="solutions"></section>
<h2 class="section-title display" style="top:722px">Our Security Solutions</h2>

<h3 class="sidebar-title display">Services</h3>
<ul class="service-list">
  <li style="top:10px">Property guards</li>
  <li style="top:48px">Corporate events security</li>
  <li style="top:85px">Personal bodyguard for high net worth individuals</li>
  <li style="top:137px">Security consultancy</li>
  <li style="top:174px">Private investigation</li>
</ul>
<div class="callout">
  <p>CUSTOM OPTIONS<br>AVAILABLE<br><b>CALL 555-019-284</b></p>
  <div class="brand"><span class="brand-mark"></span><span class="brand-name">TAVRON<small>SECURITY SERVICES LTD.</small></span></div>
</div>

<span class="col-rule" style="left:377px;top:826px;height:559px"></span>
<span class="col-rule" style="left:599px;top:826px;height:559px"></span>
<span class="col-rule" style="left:821px;top:826px;height:559px"></span>
<span class="col-rule" style="left:1043px;top:826px;height:559px"></span>
<span class="row-rule" style="left:377px;top:1074px;width:222px"></span>
<span class="row-rule" style="left:599px;top:1090px;width:222px"></span>
<span class="row-rule" style="left:821px;top:1056px;width:222px"></span>

<article class="card" style="left:392px;top:832px;height:230px">
  <h3>Property Guards</h3>
  <p>Lorem ipsum dolor sit amet, consectetuer adipiscing elit, sed diam nonummy nibh euismod tincidunt</p>
  <p>ut laoreet dolore magna aliquam erat volutpat. Ut wisi enim ad minim veniam, quis nostrud exerci tation ullamcorper suscipit lobortis nisl.</p>
  <span class="read-more" style="top:199px">Read More</span>
</article>
<article class="card" style="left:616px;top:832px;height:250px">
  <h3>Personal Bodyguards</h3>
  <p>Duis autem vel eum iriure dolor in hendrerit in vulputate velit esse molestie consequat.</p>
  <p>Vel illum dolore eu feugiat nulla facilisis at vero eros et accumsan et iusto odio dignissim qui blandit praesent luptatum zzril delenit augue duis dolore te feugait nulla facilisi.</p>
  <span class="read-more" style="top:217px">Read More</span>
</article>
<article class="card" style="left:840px;top:832px">
  <h3>Private Investigation</h3>
  <p>Ut wisi enim ad minim veniam, quis nostrud exerci tation ullamcorper suscipit lobortis nisl ut aliquip ex ea commodo consequat. Duis autem vel eum iriure dolor in hendrerit in vulputate velit</p>
  <span class="read-more" style="top:183px">Read More</span>
</article>
<article class="card" style="left:392px;top:1106px">
  <h3>Corporate Events Security</h3>
  <p>Lorem ipsum dolor sit amet, consectetuer adipiscing elit, sed diam nonummy nibh euismod tincidunt ut laoreet dolore magna aliquam erat volutpat. Ut wisi enim ad minim veniam, quis nostrud exerci tation ullamcorper suscipit lobortis nisl ut aliquip ex ea commodo consequat.</p>
  <span class="read-more" style="top:198px">Read More</span>
</article>
<article class="card" style="left:616px;top:1124px">
  <h3>Security Consultancy</h3>
  <p>Duis autem vel eum iriure dolor in hendrerit in vulputate velit esse molestie consequat, vel illum dolore eu feugiat nulla facilisis at vero eros et accumsan et iusto odio dignissim qui blandit praesent luptatum zzril delenit augue duis dolore</p>
  <span class="read-more" style="top:198px">Read More</span>
</article>
<article class="card" style="left:840px;top:1083px">
  <h3>Executive Protection</h3>
  <p>Lorem ipsum dolor sit amet, consectetuer adipiscing elit, sed diam nonummy nibh euismod tincidunt ut laoreet dolore magna aliquam erat volutpat. Ut wisi enim ad minim veniam, quis nostrud exerci tation ullamcorper suscipit lobortis nisl ut aliquip ex ea commodo consequat.</p>
  <span class="read-more" style="top:198px">Read More</span>
</article>

<h2 class="section-title display" style="top:1425px">Industries We Serve</h2>
<span class="carousel-btn" style="left:109px"><svg width="10" height="15"><path d="M8 1 2 7.5 8 14" fill="none" stroke="#fff" stroke-width="2"/></svg></span>
<span class="carousel-btn" style="left:1058px"><svg width="10" height="15"><path d="M2 1l6 6.5L2 14" fill="none" stroke="#fff" stroke-width="2"/></svg></span>
<div class="industry" style="left:157px"><div role="img" aria-label="Security officer on a university campus lawn" style="background:linear-gradient(#6f7a5a,#4d6b3a 60%,#7e8c5e)"></div></div>
<div class="industry" style="left:389px"><div role="img" aria-label="Guard patrolling a shopping centre" style="background:linear-gradient(#a58b6a,#6a5a4a 60%,#8a7a6a)"></div></div>
<div class="industry" style="left:619px"><div role="img" aria-label="Surveillance cameras over an industrial skyline" style="background:linear-gradient(#c9dbe6,#a9c3d3 60%,#8aa6b8)"></div></div>
<div class="industry" style="left:850px"><div role="img" aria-label="Operator watching security monitors" style="background:linear-gradient(#4a4a52,#2a2a30 60%,#3a3a44)"></div></div>
<span class="industry-label display" style="left:147px">Campus Security</span>
<span class="industry-label display" style="left:387px">Shoping Center</span>
<span class="industry-label display" style="left:619px">Industrial Security</span>
<span class="industry-label display" style="left:848px">Security Monitoring</span>

<footer class="site-footer"></footer>
<h3 class="footer-title display" style="left:157px">About us</h3>
<h3 class="footer-title display" style="left:539px">Quick Links</h3>
<h3 class="footer-title display" style="left:766px">Newsletter Sigup</h3>
<div class="footer-copy">
  <p>Lorem ipsum dolor sit amet, consectetur adipiscing elit. Morbi pellentesque iaculis justo eget fermentum. Pellentesque commodo iaculis neque, vitae tincidunt odio pellentesque luctus. Aenean in eros eu magna vestibulum imperdiet pretium nec augue.</p>
  <p>Etiam quis turpis enim. Vestibulum auctor id mauris vulputate consequat. Suspendisse potenti. Cras at imperdiet elit. Integer fringilla tellus non diam condimentum, sed ultricies urna ultricies. Sed congue quis dui convallis dictum. Donec malesuada vulputate risus vitae vulputate. Maecenas in congue urna. Sed porttitor bibendum</p>
</div>
<ul class="quick-links">
  <li>HOME</li><li>OUR SERVICES</li><li>ABOUT</li><li>LOCATIONS</li><li>NEWS</li><li>CAREERS</li><li>CONTACT US</li>
</ul>
<p class="newsletter-note">Fill the form below and recive our latest offers &amp; updates</p>
<div class="field" style="top:1981px">Your Name</div>
<div class="field" style="top:2028px">Your Email</div>
<div class="signup">Signup Now!</div>
<div class="footer-bar"></div>
<p class="copyright">Copyright © 2014 Tavron Security Service LTD.</p>
<div class="social dark" style="left:931px;top:2199px" aria-label="Social links"><i></i><i></i><i></i></div>

</body>
</html>
```